VELKO Website Redesign in Wix

Task:
Create a new design for all pages of the VELKO technology website in Wix. Specifications are:
Color palette preferences: black, white, gray, purple, blue. See VELKO Ref Doc provided.
Please refer to the VELKO_ref doc for a sample of the desired color palette
Typesetting must be in Montserrat
Brand will be that of a Marketing Technology company
Looking for vibrant, highly engaging images and organized, digestible flow. Open to suggestions
Required format is Wix.
VELKO logo does NOT need to be redesigned. Please use the files provided for the VELKO logo.
Look and feel
Each slider illustrates characteristics of the customer's brand and the style your logo design should communicate.

```html
<!DOCTYPE html>
<html lang="en">
<head>
<meta charset="utf-8">
<title>VELKO — Marketing Technology</title>
<link href="https://fonts.googleapis.com/css2?family=Montserrat:wght@400;500;600;700&family=Roboto:wght@400;500;700&display=swap" rel="stylesheet">
<style>
:root{
  --black:#000;
  --ink:#1b1b1b;
  --white:#fff;
  --navy:#0a1a38;
  --navy-deep:#06102a;
  --contact:#0f2d57;
  --btn:#0d2a55;
  --gray-bg:#eff0f3;
  --line:#9a9a9a;
  --text:#555;
  --footer:#141414;
  --accent:#1f7ad8;
  --brand-blue:#2d5a8c;
}
*{margin:0;padding:0;box-sizing:border-box}
html,body{width:1200px;height:3805px;overflow:hidden;background:var(--white)}
body{position:relative;font-family:"Roboto",Arial,sans-serif;color:var(--ink)}
.abs{position:absolute}
.btn{position:absolute;display:flex;align-items:center;justify-content:center;gap:5px;font:700 14px "Roboto",sans-serif;letter-spacing:.2px;text-transform:uppercase;background:var(--btn);color:var(--white)}
.btn svg{width:12px;height:12px}
/* nav */
.site-header{top:0;left:0;width:1200px;height:84px;background:var(--black)}
.site-header .brand{left:111px;top:16px;font:500 54px "Montserrat",sans-serif;color:var(--white);letter-spacing:10px;line-height:52px}
.nav a{position:absolute;top:34px;font:700 14px "Roboto",sans-serif;color:var(--white);text-decoration:none;letter-spacing:.2px}
.nav a.active{border-bottom:2px solid var(--white);padding-bottom:3px}
/* hero */
.hero-photo{top:84px;left:0;width:1200px;height:643px;background:linear-gradient(120deg,#8fb0d6 0%,#c9d6e6 35%,#e6e9ee 55%,#8098b8 80%,#31496d 100%)}
.hero-card{top:423px;left:291px;width:618px;height:304px;background:var(--white);text-align:center}
.hero-card .wordmark{margin-top:36px;font:600 112px "Montserrat",sans-serif;letter-spacing:22px;line-height:104px;color:var(--black);padding-left:22px}
.hero-card p{margin:20px auto 0;width:520px;font:400 14.5px/21px "Roboto",sans-serif;color:#444}
/* features */
.features{top:814px;left:111px;width:978px;height:367px;border:1px solid #aaa;display:flex}
.feature{flex:1;position:relative;border-right:1px solid #aaa;text-align:center}
.feature:last-child{border-right:none}
.feature h3{margin-top:34px;font:700 30px/34px "Roboto",sans-serif;color:var(--black)}
.feature p{margin:26px auto 0;width:264px;font:400 14.5px/21.5px "Roboto",sans-serif;color:var(--text);text-align:justify;text-align-last:center}
.feature .btn{left:89px;top:279px;width:146px;height:44px}
/* about */
.about-top{top:1267px;left:0;width:1200px;height:63px;background:var(--navy-deep)}
.about{top:1330px;left:0;width:1200px;height:458px;background:radial-gradient(ellipse at 50% 82%,#3f8bd8 0%,#123a74 18%,#071634 50%,#040b1e 100%)}
.about h2{position:absolute;top:55px;width:100%;text-align:center;font:700 41px "Montserrat",sans-serif;color:var(--white)}
.about p{position:absolute;top:112px;left:235px;width:730px;text-align:center;font:400 14.5px/26px "Roboto",sans-serif;color:var(--white)}
.about .btn{left:528px;top:263px;width:146px;height:45px;background:var(--white);color:var(--btn)}
/* awards */
.section-title{position:absolute;width:1200px;left:0;text-align:center;font:700 41px "Montserrat",sans-serif;color:var(--ink)}
.awards-grid{top:1938px;left:117px;width:966px;height:115px;border:1px solid #999;display:flex}
.award{flex:1;border-right:1px solid #999;display:flex;align-items:center;justify-content:center}
.award:last-child{border-right:none}
.award span{display:block;width:130px;height:44px;background:#dfe4ea}
/* testimonials */
.testimonials{top:2139px;left:0;width:1200px;height:465px;background:var(--gray-bg)}
.testimonials blockquote{position:absolute;top:142px;left:256px;width:688px;text-align:center;font:400 14.5px/21.5px "Roboto",sans-serif;color:var(--text)}
.testimonials .name{position:absolute;top:278px;width:100%;text-align:center;font:500 21px "Roboto",sans-serif;color:#333}
.testimonials .company{position:absolute;top:305px;width:100%;text-align:center;font:400 12.5px "Roboto",sans-serif;color:var(--text)}
.arrow{position:absolute;top:200px;width:20px;height:32px}
.dots{position:absolute;top:385px;left:567px;display:flex;gap:6px}
.dots i{width:11px;height:11px;border-radius:50%;background:#444;display:block}
.dots i.on{background:transparent;border:1.5px solid #444}
/* contact */
.contact{top:2604px;left:0;width:1200px;height:859px;background:var(--contact)}
.contact h2{position:absolute;top:64px;width:100%;text-align:center;font:700 41px "Montserrat",sans-serif;color:var(--white)}
.field{position:absolute;border-bottom:1px solid #b8c2d0;color:var(--white);font:400 14.5px "Roboto",sans-serif;padding-left:10px}
.submit{position:absolute;left:782px;top:339px;width:217px;height:49px;background:var(--white);color:var(--btn);display:flex;align-items:center;justify-content:center;font:700 13.5px "Roboto",sans-serif}
.map{position:absolute;left:207px;top:453px;width:792px;height:307px;background:linear-gradient(135deg,#dfe8cf 0%,#eef0e4 45%,#dfe6d3 70%,#b8d2ee 100%)}
.map-callout{position:absolute;left:440px;top:482px;width:308px;height:84px;background:var(--white);border-radius:6px;box-shadow:0 2px 6px rgba(0,0,0,.25);text-align:center;padding-top:16px;font:400 18px/26px "Roboto",sans-serif;color:#222}
/* footer */
.site-footer{top:3463px;left:0;width:1200px;height:342px;background:var(--footer);color:var(--white)}
.fcol{position:absolute;top:74px}
.fcol h4{font:700 18px "Montserrat",sans-serif;letter-spacing:.2px}
.fcol h4::after{content:"";display:block;width:30px;height:3px;background:var(--accent);margin-top:11px}
.fcol ul{list-style:none;margin-top:17px;font:400 15px/21.5px "Montserrat",sans-serif}
.fcol li.gap{margin-top:21px}
.fcol .ic{display:inline-block;width:18px;color:var(--accent);font-size:12px}
.fcol .indent{padding-left:26px}
.footer-rule{position:absolute;top:275px;left:111px;width:978px;height:1px;background:#666}
.copyright{position:absolute;top:296px;width:100%;text-align:center;font:500 13px "Montserrat",sans-serif}
</style>
</head>
<body>

<header class="abs site-header">
  <div class="abs brand">VELKO</div>
  <nav class="nav">
    <a class="active" style="left:442px">HOME</a>
    <a style="left:513px">HOW IT WORKS</a>
    <a style="left:644px">VELKO APPLICATIONS</a>
    <a style="left:813px">COMPANY</a>
    <a style="left:912px">CONTACT US</a>
    <a style="left:1026px">
      <svg width="11" height="12" viewBox="0 0 11 12" style="vertical-align:-1px"><circle cx="5.5" cy="3" r="3" fill="#fff"/><path d="M0 12c0-4 2.5-5.5 5.5-5.5S11 8 11 12z" fill="#fff"/></svg>
      LOG IN</a>
  </nav>
</header>

<div class="abs hero-photo" role="img" aria-label="Photo of colleagues looking at a tablet, overlaid with connected data points"></div>
<section class="abs hero-card">
  <div class="wordmark">VELKO</div>
  <p>Increase and perfect your connection with consumers using VELKO™'s patented self-service content delivery technology</p>
  <a class="btn" style="left:237px;top:216px;width:146px;height:44px">Learn more
    <svg viewBox="0 0 12 12"><circle cx="6" cy="6" r="6" fill="#fff"/><path d="M5 3l3 3-3 3" stroke="#0d2a55" stroke-width="1.8" fill="none"/></svg></a>
</section>

<section class="abs features">
  <article class="feature">
    <h3>Current Technology<br>vs VELKO™</h3>
    <p>Lorem ipsum dolor sit amet, consectetur adipiscing elit, sed do eiusmod tempor incididunt ut labore et dolore magna aliqua. Ut enim ad minim veniam, quis nostrud exercitation ullamco laboris nisi ut aliquip ex ea commodo</p>
    <a class="btn">Learn more <svg viewBox="0 0 12 12"><circle cx="6" cy="6" r="6" fill="#fff"/><path d="M5 3l3 3-3 3" stroke="#0d2a55" stroke-width="1.8" fill="none"/></svg></a>
  </article>
  <article class="feature">
    <h3>Our Revolutionary<br>Platform</h3>
    <p>Lorem ipsum dolor sit amet, consectetur adipiscing elit, sed do eiusmod tempor incididunt ut labore et dolore magna aliqua. Ut enim ad minim veniam, quis nostrud exercitation ullamco laboris nisi ut aliquip ex ea commodo</p>
    <a class="btn">Learn more <svg viewBox="0 0 12 12"><circle cx="6" cy="6" r="6" fill="#fff"/><path d="M5 3l3 3-3 3" stroke="#0d2a55" stroke-width="1.8" fill="none"/></svg></a>
  </article>
  <article class="feature">
    <h3>Proven Success<br>in Innovation</h3>
    <p>Lorem ipsum dolor sit amet, consectetur adipiscing elit, sed do eiusmod tempor incididunt ut labore et dolore magna aliqua. Ut enim ad minim veniam, quis nostrud exercitation ullamco laboris nisi ut aliquip ex ea commodo</p>
    <a class="btn">Learn more <svg viewBox="0 0 12 12"><circle cx="6" cy="6" r="6" fill="#fff"/><path d="M5 3l3 3-3 3" stroke="#0d2a55" stroke-width="1.8" fill="none"/></svg></a>
  </article>
</section>

<div class="abs about-top"></div>
<section class="abs about" role="img" aria-label="Glowing blue digital horizon with light arcs">
  <h2>ABOUT US</h2>
  <p>VELKO™ Technology is a revolutionary platform that uses high frequency tones (known as VELKO packets) imperceptible to the human ear.&nbsp;&nbsp; VELKO's patented technology embeds information on an audio file for a more targeted, enhanced user experience via music, video, text, virtual reality, augmented reality, and other content.&nbsp; It is a modern-day solution to an age-old problem–establishing two-way communication with a consumer rather than listening to what they have to say.</p>
  <a class="btn">Learn more <svg viewBox="0 0 12 12"><circle cx="6" cy="6" r="6" fill="#0d2a55"/><path d="M5 3l3 3-3 3" stroke="#fff" stroke-width="1.8" fill="none"/></svg></a>
</section>

<h2 class="section-title" style="top:1862px">AWARDS</h2>
<section class="abs awards-grid">
  <div class="award"><span></span></div>
  <div class="award"><span></span></div>
  <div class="award"><span></span></div>
  <div class="award"><span></span></div>
</section>

<section class="abs testimonials">
  <h2 class="section-title" style="top:69px">TESTMONIALS</h2>
  <svg class="arrow" style="left:108px" viewBox="0 0 20 32"><path d="M16 3L4 16l12 13" stroke="#333" stroke-width="3" fill="none"/></svg>
  <blockquote>“Lorem ipsum dolor sit amet, consectetur adipiscing elit, sed do eiusmod tempor incididunt ut labore et dolore magna aliqua. Ut enim ad minim veniam, quis nostrud exercitation ullamco laboris nisi ut aliquip ex ea commodo consequat. Duis aute irure dolor in reprehenderit in voluptate velit esse cillum dolore eu fugiat nulla pariatur. Excepteur sint occaecat cupidatat non proident, sunt in culpa qui officia deserunt mollit anim id est laborum.”</blockquote>
  <div class="name">John doe</div>
  <div class="company">Company name</div>
  <svg class="arrow" style="left:1070px" viewBox="0 0 20 32"><path d="M4 3l12 13L4 29" stroke="#333" stroke-width="3" fill="none"/></svg>
  <div class="dots"><i class="on"></i><i></i><i></i><i></i></div>
</section>

<section class="abs contact">
  <h2>CONTACT</h2>
  <div class="field" style="left:204px;top:146px;width:384px;height:30px">First name*</div>
  <div class="field" style="left:606px;top:146px;width:386px;height:30px">Last name*</div>
  <div class="field" style="left:204px;top:218px;width:384px;height:30px">Email*</div>
  <div class="field" style="left:606px;top:218px;width:386px;height:30px">Subject*</div>
  <div class="field" style="left:204px;top:322px;width:565px;height:64px">Message*</div>
  <div class="submit">SUBMIT NOW</div>
  <div class="map" role="img" aria-label="Road map of the central United States"></div>
  <div class="map-callout">Lorem ipsum dolor sit amet,<br>consectetur</div>
  <svg class="abs" style="left:589px;top:566px" width="22" height="30" viewBox="0 0 22 30"><path d="M11 29C4 19 1 15 1 10a10 10 0 0 1 20 0c0 5-3 9-10 19z" fill="#e31b23" stroke="#7a0a0e"/><circle cx="11" cy="10" r="3.5" fill="#7a0a0e"/></svg>
</section>

<footer class="abs site-footer">
  <div class="fcol" style="left:111px">
    <h4>QUICK LINKS</h4>
    <ul><li>Home</li><li>About us</li><li>Services</li><li>Blog</li><li>Contact us</li></ul>
  </div>
  <div class="fcol" style="left:368px">
    <h4>FAQ</h4>
    <ul><li>Sed ut perspiciatis unde</li><li>Amnis iste natus error sit</li><li>Voluptatem accusantium</li><li>Doloremque Sed ut perspiciatis</li><li>Unde omnis iste natus error</li></ul>
  </div>
  <div class="fcol" style="left:659px">
    <h4>CONTACT US</h4>
    <ul>
      <li><span class="ic"><svg width="9" height="12" viewBox="0 0 9 12"><path d="M4.5 12C1.5 8 0 6 0 4.5a4.5 4.5 0 0 1 9 0C9 6 7.5 8 4.5 12z" fill="#1f7ad8"/><circle cx="4.5" cy="4.5" r="1.6" fill="#141414"/></svg></span>&nbsp;Sed ut perspiciatis unde</li>
      <li class="indent">Amnis iste natus</li>
      <li class="gap"><span class="ic"><svg width="12" height="12" viewBox="0 0 12 12"><path d="M2.5 0l2 3-1.3 1.5a7 7 0 0 0 4.3 4.3L9 7.5l3 2-1 2C5 12 0 7 .5 1z" fill="#1f7ad8"/></svg></span>&nbsp;1-866-TRY-VELKO</li>
      <li><span class="ic"><svg width="13" height="10" viewBox="0 0 13 10"><rect width="13" height="10" rx="1" fill="#1f7ad8"/><path d="M0 1l6.5 4.5L13 1" stroke="#141414" stroke-width="1.3" fill="none"/></svg></span>&nbsp;info@velkotech.com</li>
    </ul>
  </div>
  <div class="fcol" style="left:941px">
    <h4>SOCIAL MEDIA</h4>
    <ul><li>Linkvale</li><li>Chirpline</li><li>Snapframe</li><li>Streamtube</li><li>Workmesh</li></ul>
  </div>
  <div class="footer-rule"></div>
  <div class="copyright">© Copyrights 2022 Company name | All Rights reserved</div>
</footer>

</body>
</html>
```